LM-Steuerberatung WordPress Site fully implemented (tax advisor)

Hello!
I need a little Wordpress Site for my newly founded Tax-Advisor Company.
I am a one-man Office advising in the area of Crypto-Currency.
PLEASE only provide a Design, if you can also Implement a WP-Site afterwards on an existing Webspace.

Please find the Content and Website-Description in the attached Document

Language for the Website is German (for now)

Target Market(s)

Tax-Advisory (specialized in Crypto Currency)

Coding

Coded - Design and coding required

Number of Pages Required

5+ page

Font styles to use
Sans Serif

Requirements
Must have
• Wordpress Implementation afterwards - Details according to attached Project Information Document

```html
<!DOCTYPE html>
<html lang="de">
<head>
<meta charset="utf-8">
<title>LM-Steuerberatung</title>
<link rel="stylesheet" href="https://fonts.googleapis.com/css2?family=Manrope:wght@400;500;600;700;800&display=swap">
<style>
:root{
  --navy:#1b2a44;
  --navy-deep:#161d2b;
  --ink:#1f2a3a;
  --grey:#a9a9a9;
  --white:#ffffff;
  --muted:#c9ced8;
  --accent:#2a4a8a;
  --line:#3a4558;
}
*{box-sizing:border-box;margin:0;padding:0}
html,body{width:1051px;height:1200px;overflow:hidden}
body{font-family:"Manrope",sans-serif;color:var(--ink);background:var(--white);position:relative}
.wrap{position:absolute;left:87px;right:87px}

.topbar{position:absolute;top:0;left:0;width:1051px;height:45px;background:var(--navy)}
.topbar .socials{position:absolute;left:87px;top:16px;display:flex;gap:14px}
.social-dot{width:13px;height:13px;border-radius:50%;background:var(--white)}
.topbar .contact{position:absolute;right:87px;top:13px;display:flex;gap:16px;color:var(--white);font-size:14px}
.topbar .contact span{display:flex;align-items:center;gap:6px}

.navbar{position:absolute;top:45px;left:0;width:1051px;height:79px;background:var(--white)}
.brand{position:absolute;left:87px;top:27px;display:flex;align-items:center;gap:8px;font-weight:800;font-size:17px;letter-spacing:.3px;color:var(--navy)}
.brand .mark{width:22px;height:22px;background:var(--navy)}
.menu{position:absolute;right:87px;top:20px;display:flex;align-items:center;font-size:14.5px;font-weight:500;color:var(--ink)}
.menu a{color:inherit;text-decoration:none;margin-right:38px;position:relative}
.menu a.active::after{content:"";position:absolute;left:50%;top:24px;width:6px;height:6px;margin-left:-3px;border-radius:50%;background:var(--navy)}
.menu .cta{margin:0;background:var(--navy);color:var(--white);font-weight:600;padding:10px 30px;border-radius:16px 4px 16px 4px;width:111px;text-align:center}

.hero{position:absolute;top:124px;left:0;width:1051px;height:473px;background:linear-gradient(90deg,#5c5e62 0%,#9ea2a6 35%,#b9bdc0 60%,#8f9aa8 85%,#7d8896 100%)}
.hero-inner{position:absolute;top:138px;left:0;width:100%;text-align:center;color:var(--white)}
.hero .kicker{font-size:24px;font-weight:600}
.hero h1{font-size:46px;font-weight:800;margin-top:4px;line-height:1.1}
.hero p{font-size:16px;line-height:29px;margin:12px auto 0;width:540px}
.hero .btn{display:inline-flex;align-items:center;gap:8px;margin-top:10px;background:var(--navy);padding:12px 24px;border-radius:20px 4px 20px 4px;font-size:15px;font-weight:600}
.arrow{position:absolute;top:222px}
.arrow.left{left:84px}.arrow.right{right:84px}
.dots{position:absolute;top:432px;left:466px;display:flex;gap:12px}
.dots i{width:31px;height:2px;background:rgba(255,255,255,.55)}
.dots i.on{background:var(--white)}

.steps{position:absolute;top:667px;left:87px;right:87px;display:flex;justify-content:space-between}
.step{display:flex;align-items:center;gap:16px;width:262px}
.step .num{flex:none;width:70px;height:103px;display:flex;align-items:center;justify-content:center;background:var(--navy);color:var(--white);font-weight:700;font-size:20px;border-radius:6px}
.step p{font-size:13.5px;line-height:19.5px;color:var(--ink)}

.footer{position:absolute;top:864px;left:0;width:1051px;height:336px;background:var(--navy-deep);color:var(--white)}
.f-brand{position:absolute;left:87px;top:62px;display:flex;align-items:center;gap:10px;font-weight:800;font-size:18px;letter-spacing:.3px}
.f-brand .mark{width:22px;height:22px;background:var(--white)}
.f-about{position:absolute;left:87px;top:117px;width:270px;font-size:14.5px;line-height:22.5px;color:var(--muted)}
.f-socials{position:absolute;left:87px;top:214px;display:flex;gap:24px}
.f-socials .social-dot{width:16px;height:16px}
.divider{position:absolute;top:68px;width:1px;height:180px;background:var(--line)}
.divider::before{content:"";position:absolute;left:-4px;top:31px;width:4px;height:18px;background:var(--accent)}
.col{position:absolute;top:70px}
.col h4{font-size:15px;font-weight:700;margin-bottom:14px}
.col ul{list-style:none;font-size:14.5px;color:var(--muted)}
.col li{height:34px}
.col li span{display:inline-flex;align-items:center;gap:10px}
.bottom{position:absolute;left:85px;right:87px;top:283px;border-top:1px solid var(--line)}
.copy{position:absolute;top:300px;width:100%;text-align:center;font-size:13.5px;color:var(--muted)}
.copy b{color:var(--white);font-weight:600}
</style>
</head>
<body>

<header class="topbar">
  <div class="socials">
    <span class="social-dot" aria-label="Social-Profil"></span>
    <span class="social-dot" aria-label="Social-Profil"></span>
    <span class="social-dot" aria-label="Social-Profil"></span>
  </div>
  <div class="contact">
    <span><svg width="13" height="13" viewBox="0 0 24 24" fill="#fff"><path d="M6.6 10.8a15 15 0 0 0 6.6 6.6l2.2-2.2a1 1 0 0 1 1-.25 11.4 11.4 0 0 0 3.6.57 1 1 0 0 1 1 1V20a1 1 0 0 1-1 1A17 17 0 0 1 3 4a1 1 0 0 1 1-1h3.5a1 1 0 0 1 1 1c0 1.25.2 2.45.57 3.57a1 1 0 0 1-.25 1z"/></svg>+43 512 000 471</span>
    <span><svg width="14" height="11" viewBox="0 0 24 18" fill="#fff"><path d="M0 0h24v2L12 10 0 2z"/><path d="M0 4l12 8 12-8v14H0z"/></svg>office@lm-steuer.example</span>
  </div>
</header>

<nav class="navbar">
  <div class="brand"><span class="mark"></span>LM STEUERBERATUNG</div>
  <div class="menu">
    <a class="active">Home</a>
    <a>Leistungen</a>
    <a>Über mich</a>
    <a>Impressum</a>
    <a class="cta">Kontakt</a>
  </div>
</nav>

<section class="hero" role="img" aria-label="Foto: Beratungsgespräch zwischen drei Personen an einem Bürotisch">
  <svg class="arrow left" width="22" height="34" viewBox="0 0 22 34"><path d="M18 3 5 17l13 14" stroke="#fff" stroke-width="5" fill="none" stroke-linecap="round" stroke-linejoin="round"/></svg>
  <svg class="arrow right" width="22" height="34" viewBox="0 0 22 34"><path d="M4 3l13 14L4 31" stroke="#fff" stroke-width="5" fill="none" stroke-linecap="round" stroke-linejoin="round"/></svg>
  <div class="hero-inner">
    <div class="kicker">Willkommen</div>
    <h1>bei LM-Steuerberatung!</h1>
    <p>Ihrem Spezialisten bei allen steuerlichen Themen rund um Einkünfte &amp; Vermögen aus Krypto-Assets.</p>
    <span class="btn">Weiter zu unseren Leistungen
      <svg width="13" height="13" viewBox="0 0 24 24"><circle cx="12" cy="12" r="12" fill="#fff"/><path d="M10 7l5 5-5 5" stroke="#1b2a44" stroke-width="3" fill="none" stroke-linecap="round"/></svg>
    </span>
  </div>
  <div class="dots"><i class="on"></i><i></i><i></i></div>
</section>

<section class="steps">
  <div class="step"><span class="num">01</span><p>Dann mach ich eine Schweizer Holding-Gesellschaft– dort zahlt man fast keine Steuern</p></div>
  <div class="step"><span class="num">02</span><p>Dann melde ich einfach meinen Hauptwohnsitz in Österreich ab</p></div>
  <div class="step"><span class="num">03</span><p>Dann lass ich meine Kryptos auf einer Börse in Singapur, dort ist das steuerfrei</p></div>
</section>

<footer class="footer">
  <div class="f-brand"><span class="mark"></span>LM STEUERBERATUNG</div>
  <p class="f-about">Ihrem Spezialisten bei allen steuerlichen Themen rund um Einkünfte &amp; Vermögen aus Krypto-Assets.</p>
  <div class="f-socials">
    <span class="social-dot" aria-label="Social-Profil"></span>
    <span class="social-dot" aria-label="Social-Profil"></span>
    <span class="social-dot" aria-label="Social-Profil"></span>
  </div>

  <span class="divider" style="left:450px"></span>
  <div class="col" style="left:537px">
    <h4>QUICK LINKS</h4>
    <ul><li>Home</li><li>Leistungen</li><li>Über mich</li><li>Impressum</li><li>Kontakt</li></ul>
  </div>

  <span class="divider" style="left:718px"></span>
  <div class="col" style="left:793px">
    <h4>CONTACT US</h4>
    <ul>
      <li><span><svg width="14" height="11" viewBox="0 0 24 18" fill="#8d93a0"><path d="M0 0h24v2L12 10 0 2z"/><path d="M0 4l12 8 12-8v14H0z"/></svg>office@lm-steuer.example</span></li>
      <li><span><svg width="13" height="13" viewBox="0 0 24 24" fill="#8d93a0"><path d="M6.6 10.8a15 15 0 0 0 6.6 6.6l2.2-2.2a1 1 0 0 1 1-.25 11.4 11.4 0 0 0 3.6.57 1 1 0 0 1 1 1V20a1 1 0 0 1-1 1A17 17 0 0 1 3 4a1 1 0 0 1 1-1h3.5a1 1 0 0 1 1 1c0 1.25.2 2.45.57 3.57a1 1 0 0 1-.25 1z"/></svg>+43 512 000 471</span></li>
    </ul>
  </div>

  <div class="bottom"></div>
  <p class="copy">© 2022 <b>LM-Steuerberatung</b>. All right reserved</p>
</footer>

</body>
</html>
```